Camp Maplebrook 2018

We need a postcard design to advertise our summer programs. We are a Christian camp with day camp and overnight camps.

Target Market(s)

parents of elementary age kids

Industry/Entity Type

Christian

Colors
ec1f27
f37122
faa54b
fbee3d
f78f20
f04a50
fbed22
fbee3e

Requirements
Must have
• Day Camp 2018 "Shine Bright Daily"
• June 25 - August 24
• $135 per week
• Mon-Fri 8 am to 4 pm. Open to all kids entering grades 1 to 8. Day camp is chock full of activities like swimming, rock wall, archery, sports, crafts, air rifles and much more! Daily lunch and snack included. Before and after-care available at an extra rate.
• Register and pay in full by April 1st, save $270!
• Overnight Camp 2018
• July 15 - 21 & July 22 - 28
• $330 per week
• Open to all kids ages 8 to 14. Spend the week making new friends, sleeping in cabins, climbing the rock wall and swimming at the beach! Our guest speakers will lead twice daily chapel sessions that will challenge campers to grow in their faith.
• 42 Cedar Vale Rd. Millbrook, VT 05819
• 603-418-5926
• www.maplebrook.org
Nice to have
• bright and colorful

```html
<!DOCTYPE html>
<html lang="en">
<head>
<meta charset="utf-8">
<title>Camp Maplebrook 2018 Postcard</title>
<link rel="stylesheet" href="https://fonts.googleapis.com/css2?family=Fredoka:wght@400;600;700&family=Open+Sans:ital,wght@0,400;0,700;1,700&family=Righteous&family=Rubik+Dirt&display=swap">
<style>
  :root {
    --backdrop: #b9e9cc;
    --teal-dark: #0f7a6a;
    --teal-mid: #3bb3a0;
    --teal-pale: #e3f4f1;
    --red: #ec1f27;
    --orange: #f37122;
    --gold: #f7c948;
    --gold-deep: #c8901c;
    --ink: #1a1a1a;
    --paper: #ffffff;
    --water-light: #bfeff0;
    --water-deep: #3aaab4;
  }
  * { box-sizing: border-box; margin: 0; padding: 0; }
  html, body { width: 1200px; height: 696px; overflow: hidden; }
  body {
    background: var(--backdrop);
    font-family: "Open Sans", sans-serif;
    color: var(--ink);
    position: relative;
  }
  .card {
    position: absolute;
    top: 160px;
    width: 564px;
    height: 376px;
    background: var(--paper);
    overflow: hidden;
  }
  .card--back { left: 24px; background: linear-gradient(135deg, var(--teal-pale), var(--paper) 45%); }
  .card--front { left: 612px; }

  /* Back side */
  .back-info { position: absolute; left: 0; top: 14px; width: 340px; text-align: center; }
  .back-info .note { font-size: 11px; line-height: 1.55; }
  .early-band {
    margin-top: 6px; background: var(--teal-dark); color: var(--paper);
    font-weight: 700; font-style: italic; font-size: 11.5px; padding: 3px 0;
  }
  .overnight-title { font-family: "Righteous", sans-serif; font-weight: 400; font-size: 17px; letter-spacing: 2px; margin-top: 4px; }
  .date-band { background: var(--teal-mid); color: var(--paper); font-weight: 700; font-style: italic; font-size: 11.5px; padding: 3px 0; }
  .overnight-price { font-family: "Righteous", sans-serif; font-size: 15px; letter-spacing: 2px; margin-top: 6px; }
  .hex-row { display: flex; justify-content: center; gap: 14px; margin-top: 6px; }
  .hex-item { display: flex; flex-direction: column; align-items: center; }
  .hex {
    width: 78px; height: 70px;
    clip-path: polygon(25% 0, 75% 0, 100% 50%, 75% 100%, 25% 100%, 0 50%);
    background: var(--paper); padding: 3px;
  }
  .hex span {
    display: block; width: 100%; height: 100%;
    clip-path: polygon(25% 0, 75% 0, 100% 50%, 75% 100%, 25% 100%, 0 50%);
  }
  .hex-label { font-weight: 700; font-size: 11px; color: var(--teal-dark); margin-top: 2px; white-space: nowrap; }
  .photo-friends { background: linear-gradient(160deg, #8cc86a, #f2a5b8); }
  .photo-cabin { background: linear-gradient(160deg, #d9d7d2, #8f8b86); }
  .photo-swim { background: linear-gradient(160deg, #5cc3e0, #1e7fb4); }
  .photo-rock { background: linear-gradient(160deg, #a8a39b, #e0782d); }
  .photo-archery { background: linear-gradient(160deg, #8ec6ea, #5a9a4c); }
  .photo-crafts { background: linear-gradient(160deg, #f7f3ea, #f1c33c); }
  .photo-rifles { background: linear-gradient(160deg, #c9c2b3, #7a5a3c); }

  .divider { position: absolute; left: 344px; top: 0; width: 1px; height: 320px; background: #666; }
  .stamp-box { position: absolute; right: 18px; top: 22px; width: 92px; height: 62px; border: 1px solid #555; }
  .address-lines { position: absolute; left: 366px; top: 190px; width: 176px; }
  .address-lines span { display: block; height: 1px; background: #555; margin-bottom: 30px; }

  .contact-row {
    position: absolute; left: 14px; bottom: 28px;
    display: flex; align-items: center; gap: 6px; font-size: 12.5px;
  }
  .contact-row svg { width: 12px; height: 12px; }
  .contact-row .gap { width: 8px; }
  .web-tab {
    position: absolute; right: 0; bottom: 8px; width: 170px; height: 24px;
    background: var(--teal-dark); color: var(--paper);
    font-weight: 700; font-size: 12.5px; display: flex; align-items: center; justify-content: center;
    border-radius: 10px 0 0 10px;
  }

  /* Front side */
  .front-frame { position: absolute; inset: 6px; border: 2px solid var(--teal-dark); }
  .pool-photo {
    position: absolute; left: 8px; top: 8px; right: 8px; bottom: 70px;
    background: linear-gradient(180deg, var(--water-deep), var(--water-light) 70%, #e6f8f6);
  }
  .seal { position: absolute; left: 30px; top: 18px; width: 104px; height: 104px; }
  .headline { position: absolute; left: 100px; right: 20px; top: 150px; text-align: center; }
  .day-camp { font-family: "Fredoka", sans-serif; font-weight: 700; font-size: 28px; line-height: 1.2; color: var(--ink); }
  .tagline {
    font-family: "Rubik Dirt", sans-serif; font-size: 34px; color: var(--teal-dark);
    letter-spacing: 1px; line-height: 1.1; white-space: nowrap;
  }
  .schedule {
    position: absolute; left: 36px; top: 240px;
    font-family: "Fredoka", sans-serif; font-weight: 700; font-size: 27px; line-height: 1.1;
    color: var(--red);
    text-shadow: 2px 2px 0 var(--paper), -1px -1px 0 var(--paper);
  }
  .brand {
    position: absolute; left: 292px; top: 246px; width: 250px;
    display: flex; align-items: center; gap: 8px;
  }
  .brand-dot { flex: none; width: 16px; height: 16px; border-radius: 50%; background: var(--orange); }
  .brand-name { font-family: "Fredoka", sans-serif; font-weight: 700; font-size: 24px; line-height: 1.05; color: var(--red); }
  .front-band {
    position: absolute; left: 8px; right: 8px; bottom: 8px; height: 62px; background: var(--teal-dark);
  }
  .grades {
    position: absolute; left: 20px; bottom: 22px; width: 200px; text-align: center;
    color: var(--paper); font-weight: 700; font-size: 12.5px; line-height: 1.35;
  }
  .activity-row { position: absolute; right: 14px; bottom: 12px; display: flex; gap: 8px; }
  .activity-row .hex { width: 58px; height: 52px; }
  .activity-row .hex-label { color: var(--paper); font-size: 10.5px; }
</style>
</head>
<body>

  <section class="card card--back" aria-label="Postcard back">
    <div class="back-info">
      <p class="note">Daily lunch and snack included.<br>Before and after-care available at an extra rate.</p>
      <p class="early-band">Register and pay in full by April 1st, save $270!</p>
      <h2 class="overnight-title">OVERNIGHT CAMP 2018</h2>
      <p class="date-band">July 15 - 21 &amp; July 22 to 28</p>
      <p class="overnight-price">$330 PER WEEK</p>
      <div class="hex-row">
        <div class="hex-item">
          <div class="hex"><span class="photo-friends" role="img" aria-label="Photo of campers making new friends"></span></div>
          <p class="hex-label">New Friends</p>
        </div>
        <div class="hex-item">
          <div class="hex"><span class="photo-cabin" role="img" aria-label="Photo of a cabin bunk room"></span></div>
          <p class="hex-label">Sleeping in Cabin</p>
        </div>
        <div class="hex-item">
          <div class="hex"><span class="photo-swim" role="img" aria-label="Photo of a camper swimming"></span></div>
          <p class="hex-label">Swimming</p>
        </div>
      </div>
    </div>

    <div class="divider"></div>
    <div class="stamp-box"></div>
    <div class="address-lines"><span></span><span></span><span></span><span></span></div>

    <div class="contact-row">
      <svg viewBox="0 0 12 12" aria-hidden="true"><circle cx="6" cy="6" r="5.2" fill="none" stroke="#1a1a1a"/><path d="M6 2.6a2 2 0 0 1 2 2c0 1.6-2 4-2 4s-2-2.4-2-4a2 2 0 0 1 2-2z" fill="#1a1a1a"/></svg>
      <span>42 Cedar Vale Rd. Millbrook, VT 05819</span>
      <span class="gap"></span>
      <svg viewBox="0 0 12 12" aria-hidden="true"><circle cx="6" cy="6" r="5.2" fill="none" stroke="#1a1a1a"/><path d="M4 3.2l1 1.6-.6.7a4 4 0 0 0 2 2l.7-.6 1.6 1-.6 1C6 8.6 3.4 6 3.1 4z" fill="#1a1a1a"/></svg>
      <span>603-418-5926</span>
    </div>
    <div class="web-tab">www.maplebrook.org</div>
  </section>

  <section class="card card--front" aria-label="Postcard front">
    <div class="pool-photo" role="img" aria-label="Photo of two children swimming underwater in a pool"></div>
    <div class="front-frame"></div>

    <svg class="seal" viewBox="0 0 104 104" aria-label="June 25 - August 24, $135 per week">
      <defs>
        <radialGradient id="goldFill" cx="40%" cy="35%" r="70%">
          <stop offset="0" stop-color="#fff3b0"/>
          <stop offset="0.6" stop-color="#f7c948"/>
          <stop offset="1" stop-color="#c8901c"/>
        </radialGradient>
        <path id="sealArc" d="M14 52a38 38 0 0 1 76 0"/>
      </defs>
      <circle cx="52" cy="52" r="50" fill="url(#goldFill)"/>
      <circle cx="52" cy="55" r="29" fill="none" stroke="#1a1a1a" stroke-width="1.5"/>
      <text font-family="Fredoka, sans-serif" font-weight="600" font-size="11" fill="#1a1a1a">
        <textPath href="#sealArc" startOffset="50%" text-anchor="middle">June 25 - August 24</textPath>
      </text>
      <g font-family="Fredoka, sans-serif" font-weight="700" fill="#1a1a1a" text-anchor="middle">
        <text x="52" y="44" font-size="12">$</text>
        <text x="52" y="56" font-size="13">135</text>
        <text x="52" y="67" font-size="11">per</text>
        <text x="52" y="78" font-size="11">week</text>
      </g>
    </svg>

    <div class="headline">
      <h1 class="day-camp">Day Camp 2018</h1>
      <p class="tagline">SHINE BRIGHT DAILY</p>
    </div>

    <p class="schedule">Mon to Fri<br>8 am to 4 pm</p>

    <div class="brand">
      <span class="brand-dot"></span>
      <span class="brand-name">Camp<br>Maplebrook</span>
    </div>

    <div class="front-band"></div>
    <p class="grades">Open to all kids entering<br>grades 1 to 8</p>
    <div class="activity-row">
      <div class="hex-item">
        <div class="hex"><span class="photo-swim" role="img" aria-label="Photo of a child swimming"></span></div>
        <p class="hex-label">Swimming</p>
      </div>
      <div class="hex-item">
        <div class="hex"><span class="photo-rock" role="img" aria-label="Photo of a child on a climbing wall"></span></div>
        <p class="hex-label">Rock Wall</p>
      </div>
      <div class="hex-item">
        <div class="hex"><span class="photo-archery" role="img" aria-label="Photo of campers doing archery"></span></div>
        <p class="hex-label">Archery</p>
      </div>
      <div class="hex-item">
        <div class="hex"><span class="photo-crafts" role="img" aria-label="Photo of painted craft jars"></span></div>
        <p class="hex-label">Crafts</p>
      </div>
      <div class="hex-item">
        <div class="hex"><span class="photo-rifles" role="img" aria-label="Photo of a camper at air rifle practice"></span></div>
        <p class="hex-label">Air Rifles</p>
      </div>
    </div>
  </section>

</body>
</html>
```